American cannabis tech company business card design

Pavrel.com is seeking a modern, professional, and brand-aligned business card that represents our company and its core values: Mission, Story, Values, and Impact. As an innovative cannabis company, we want a business card that is not only visually appealing but also serves as a representation of who we are and what we stand for.

Project Scope: Design a double-sided business card that integrates our brand identity and core values. Incorporate our key brand elements, ensuring a sleek and contemporary aesthetic. Visually reflect our core values (Mission, Story, Values, Impact) in a way that is engaging yet professional.

Target Market(s)

Vendors, third parties,

Contact Information for Business Card

Contact details (name, title, email, phone, website, etc.)

Font styles to use
Other font styles liked:
• Caslon, Centra

Colors

Designer to choose colors to be used in the design.

Requirements
Must have
• Pavrel.com logo and branding A creative yet clean way to integrate our core values (Mission, Story, Values, Impact) Modern typography and a well-structured layout
Nice to have
• forest green, grey, white, black
Should not have
• references to marijuana, leafs, plants, or related product

```html
<!DOCTYPE html>
<html lang="en">
<head>
<meta charset="UTF-8">
<title>Pavrel.com — Business Card</title>
<link href="https://fonts.googleapis.com/css2?family=Poppins:wght@400;500;700;800&display=swap" rel="stylesheet">
<style>
  :root {
    --forest: #1c3320;
    --forest-deep: #18301c;
    --paper: #ffffff;
    --cream: #fbf8f3;
    --ink: #2b2b2b;
    --stage: #e6e7e6;
  }
  * { margin: 0; padding: 0; box-sizing: border-box; }
  html, body {
    width: 1200px; height: 880px; overflow: hidden;
    background: var(--stage);
    font-family: "Poppins", sans-serif;
  }
  .sheet {
    position: relative; width: 1200px; height: 880px;
  }
  .card {
    position: absolute; left: 250px; width: 700px; height: 400px;
    border-radius: 22px; overflow: hidden;
    box-shadow: 0 6px 18px rgba(0,0,0,0.12);
  }
  /* Back side */
  .card--back { top: 25px; background: var(--forest); color: var(--cream); }
  .card--back .wordmark {
    position: absolute; left: 0; right: 0; top: 118px;
    text-align: center; font-weight: 800; font-size: 104px;
    letter-spacing: 2px; line-height: 1; color: var(--cream);
  }
  .card--back .site {
    position: absolute; left: 0; right: 0; top: 270px;
    text-align: center; font-size: 15px; letter-spacing: 4px;
    color: var(--cream);
  }
  /* Front side */
  .card--front { top: 455px; background: var(--paper); color: var(--forest); }
  .card--front .wordmark {
    position: absolute; left: 70px; top: 140px; width: 320px;
    text-align: center; font-weight: 800; font-size: 72px;
    letter-spacing: 1px; line-height: 1; color: var(--forest);
  }
  .divider {
    position: absolute; left: 418px; top: 92px;
    width: 1.5px; height: 150px; background: var(--ink);
  }
  .contact { position: absolute; left: 442px; top: 92px; }
  .contact .name {
    font-weight: 700; font-size: 19px; line-height: 1.1; color: var(--forest);
    text-transform: uppercase;
  }
  .contact .title { font-size: 14px; color: var(--ink); margin-bottom: 14px; }
  .contact .line {
    display: flex; align-items: center; gap: 9px;
    font-size: 14px; line-height: 22px; color: var(--ink);
  }
  .contact .line svg { width: 12px; height: 12px; flex: none; }
  .social {
    position: absolute; right: 36px; top: 236px;
    display: flex; gap: 12px;
  }
  .social span {
    width: 26px; height: 26px; border-radius: 5px; background: var(--forest);
    display: block;
  }
  .values-band {
    position: absolute; left: 0; top: 290px; width: 600px; height: 32px;
    background: var(--forest); color: var(--paper);
    font-size: 16px; letter-spacing: 4px;
    display: flex; align-items: center; padding-left: 30px;
  }
  .values-rule {
    position: absolute; left: 0; top: 328px; width: 612px; height: 2px;
    background: var(--forest);
  }
</style>
</head>
<body>
<main class="sheet">
  <section class="card card--back" aria-label="Card back">
    <div class="wordmark">PAVREL</div>
    <div class="site">www.PAVREL.com</div>
  </section>

  <section class="card card--front" aria-label="Card front">
    <div class="wordmark">PAVREL</div>
    <div class="divider"></div>
    <div class="contact">
      <div class="name">Daniel R. Carter</div>
      <div class="title">Director</div>
      <div class="line">
        <svg viewBox="0 0 24 24"><path fill="#1c3320" d="M6.6 10.8a15.1 15.1 0 0 0 6.6 6.6l2.2-2.2c.3-.3.7-.4 1-.2 1.1.4 2.3.6 3.6.6.6 0 1 .4 1 1V20c0 .6-.4 1-1 1A17 17 0 0 1 3 4c0-.6.4-1 1-1h3.5c.6 0 1 .4 1 1 0 1.3.2 2.5.6 3.6.1.3 0 .7-.2 1z"/></svg>
        +1 405 -555-0187
      </div>
      <div class="line">
        <svg viewBox="0 0 24 24"><path fill="#1c3320" d="M2 5h20v14H2z"/><path fill="none" stroke="#fff" stroke-width="2" d="M2 5l10 8 10-8"/></svg>
        team@pavrel.com
      </div>
      <div class="line">
        <svg viewBox="0 0 24 24"><g fill="none" stroke="#1c3320" stroke-width="2"><circle cx="12" cy="12" r="10"/><path d="M2 12h20M12 2c3 3 3 17 0 20M12 2c-3 3-3 17 0 20"/></g></svg>
        www.PAVREL.com
      </div>
    </div>
    <div class="social" aria-label="Social profiles">
      <span></span><span></span><span></span>
    </div>
    <div class="values-band">Mission | Story | Values and Impact</div>
    <div class="values-rule"></div>
  </section>
</main>
</body>
</html>
```